Stylish new business card needed!

Hello everyone! I am in need of a new business card design for an alarm company here in Hurricane WV. I have all fonts, color codes and logos provided for you use! We are a young company and like the style of a clean sleek looking business card. Would like it double sided, one side holding the logo and the other with your design!
Target Market(s)
The people that are looking for the newest tech for home automation and security
Industry/Entity Type
Alarm services; Home automation
Contact Information for Business Card
Name of person; position (Sales; Installer); Phone Number (555.418.7260); Employee cell Number; Website (www.GuardedByVelk.example); Employee Email; Double sided
Look and feel
Each slider illustrates characteristics of the customer's brand and the style your logo design should communicate.

```html
<!DOCTYPE html>
<html lang="en">
<head>
<meta charset="utf-8">
<title>Guarded by Velk – Business Card</title>
<link href="https://fonts.googleapis.com/css2?family=Roboto:wght@400;700;900&display=swap" rel="stylesheet">
<style>
  :root {
    --stage: #222222;
    --orange: #f4914f;
    --orange-deep: #e9803d;
    --grey: #9b9b9b;
    --white: #ffffff;
    --card-w: 520px;
    --card-h: 297px;
  }
  * { box-sizing: border-box; margin: 0; padding: 0; }
  html, body {
    width: 1200px; height: 780px; overflow: hidden;
    background: var(--stage);
    font-family: "Roboto", Arial, sans-serif;
  }
  .stage { position: relative; width: 1200px; height: 780px; }
  .card {
    position: absolute;
    width: var(--card-w); height: var(--card-h);
    overflow: hidden;
    box-shadow: 0 14px 30px rgba(0,0,0,.55);
  }
  /* Back side */
  .card--back { left: 60px; top: 70px; background: var(--orange); }
  .back__pattern {
    position: absolute; inset: 0;
    background: linear-gradient(135deg, var(--orange) 0%, var(--orange-deep) 100%);
  }
  .back__brand {
    position: absolute; right: 92px; top: 118px;
    color: var(--white); font-weight: 700;
    font-size: 15px; line-height: 1.1; letter-spacing: .5px;
    text-transform: uppercase; text-align: left;
  }
  /* Front side */
  .card--front { left: 620px; top: 410px; background: var(--orange); }
  .front__shape { position: absolute; inset: 0; }
  .front__identity {
    position: absolute; left: 0; top: 36px;
    display: flex; align-items: stretch;
  }
  .front__identity-bar { width: 18px; background: var(--grey); margin-right: 12px; }
  .front__name { color: var(--white); font-weight: 900; font-size: 25px; line-height: 1.1; }
  .front__role { color: var(--white); font-weight: 700; font-size: 15px; margin-top: 2px; }
  .front__contacts {
    position: absolute; left: 100px; bottom: 22px;
    list-style: none; color: var(--white);
    font-size: 14px; line-height: 1.4;
  }
  .front__contacts li { display: flex; align-items: center; gap: 8px; }
  .front__contacts svg { width: 12px; height: 12px; flex: none; }
  .front__brand {
    position: absolute; left: 332px; right: 14px; top: 72px;
    text-align: center;
  }
  .front__brand-name {
    color: var(--grey); font-weight: 700; text-transform: uppercase;
    font-size: 18px; line-height: 1; letter-spacing: 1px;
  }
  .front__brand-name span { display: block; font-size: 50px; letter-spacing: 3px; margin-top: 4px; }
  .front__tagline {
    margin-top: 8px; color: var(--orange); font-weight: 900;
    font-size: 7px; letter-spacing: .3px; text-transform: uppercase;
    white-space: nowrap;
  }
</style>
</head>
<body>
<main class="stage">
  <section class="card card--back" aria-label="Card back">
    <div class="back__pattern" role="img" aria-label="Repeating pattern of the brand wordmark in embossed orange tones"></div>
    <p class="back__brand">Guarded by<br>Velk</p>
  </section>

  <section class="card card--front" aria-label="Card front">
    <svg class="front__shape" viewBox="0 0 520 297" preserveAspectRatio="none" aria-hidden="true">
      <path d="M272,0 C250,120 330,240 410,297 L520,297 L520,0 Z" fill="var(--grey)"/>
      <path d="M290,0 C272,120 352,240 432,297 L520,297 L520,0 Z" fill="var(--white)"/>
    </svg>

    <div class="front__identity">
      <div class="front__identity-bar"></div>
      <div>
        <h1 class="front__name">Marta Kovalenko</h1>
        <p class="front__role">Sales; Installer</p>
      </div>
    </div>

    <ul class="front__contacts">
      <li>
        <svg viewBox="0 0 16 16" aria-hidden="true"><path fill="#fff" d="M3 1l3 3-2 2c1 2 4 5 6 6l2-2 3 3-2 2C7 15 1 9 1 3z"/></svg>
        555.418.7260
      </li>
      <li>
        <svg viewBox="0 0 16 16" aria-hidden="true"><rect x="4" y="1" width="8" height="14" rx="1.5" fill="none" stroke="#fff" stroke-width="1.5"/></svg>
        555.418.9031
      </li>
      <li>
        <svg viewBox="0 0 16 16" aria-hidden="true"><circle cx="8" cy="8" r="6.5" fill="none" stroke="#fff" stroke-width="1.5"/><path d="M1.5 8h13M8 1.5c-3 3.5-3 9.5 0 13M8 1.5c3 3.5 3 9.5 0 13" fill="none" stroke="#fff" stroke-width="1.2"/></svg>
        www.GuardedByVelk.example
      </li>
      <li>
        <svg viewBox="0 0 16 16" aria-hidden="true"><rect x="1" y="3" width="14" height="10" fill="none" stroke="#fff" stroke-width="1.5"/><path d="M1 3l7 6 7-6" fill="none" stroke="#fff" stroke-width="1.5"/></svg>
        info@GuardedByVelk.example
      </li>
    </ul>

    <div class="front__brand">
      <p class="front__brand-name">Guarded by<span>Velk</span></p>
      <p class="front__tagline">Automation and security services</p>
    </div>
  </section>
</main>
</body>
</html>
```